Mosquito and outdoor pest management

The uploaded logo must be integrated as the main theme of the card. I would like it to be modern and eye catching. Maybe some backround images or light silver metallic background.
Space enough at the base for contact info to be put in- phone numbers,emails,names,website.
Space on the back for short blog and lines for hand writing..calling card.
Commercial- golf courses, schools, outdoor function properties, pre event treatments.
Residential- retirement villages, townhome complexes and general houses
Management

```html
<!DOCTYPE html>
<html lang="en">
<head>
<meta charset="utf-8">
<title>Bayline Pest Care – Business Card</title>
<link rel="stylesheet" href="https://fonts.googleapis.com/css2?family=Open+Sans:wght@400;600;700&display=swap">
<style>
  :root {
    --backdrop: #e9e7e4;
    --card: #ffffff;
    --accent: #e0262b;
    --ink: #1c1c1c;
    --rule: #111111;
  }
  * { margin: 0; padding: 0; box-sizing: border-box; }
  html, body { width: 1200px; height: 1000px; overflow: hidden; }
  body {
    background: var(--backdrop);
    font-family: "Open Sans", Arial, sans-serif;
    color: var(--ink);
    position: relative;
  }
  .card {
    position: absolute;
    left: 265px;
    width: 665px;
    height: 397px;
    background: var(--card);
    border-radius: 22px;
    box-shadow: 0 4px 14px rgba(0,0,0,0.18);
  }
  .card--front { top: 73px; }
  .card--back { top: 533px; }

  .holder { position: absolute; left: 33px; top: 68px; }
  .holder__name { color: var(--accent); font-weight: 700; font-size: 22px; line-height: 28px; }
  .holder__role { font-size: 16px; line-height: 22px; }

  .contacts { position: absolute; left: 33px; top: 158px; list-style: none; }
  .contacts li { display: flex; align-items: center; height: 23.5px; font-size: 16px; }
  .contacts svg { width: 14px; height: 14px; margin-right: 7px; fill: var(--accent); flex: none; }

  .address { position: absolute; left: 33px; top: 269px; font-size: 16px; line-height: 22.5px; font-style: normal; }

  .brand {
    position: absolute;
    display: flex;
    align-items: center;
    gap: 10px;
    color: var(--ink);
    font-weight: 600;
  }
  .brand__dot { width: 16px; height: 16px; border-radius: 50%; background: var(--accent); flex: none; }
  .brand__name { font-size: 28px; line-height: 34px; letter-spacing: 0.5px; white-space: nowrap; }
  .card--front .brand { left: 300px; top: 70px; }
  .card--back .brand { left: 172px; top: 58px; }

  .write-lines { position: absolute; left: 32px; top: 197px; width: 602px; }
  .write-lines span { display: block; height: 2px; background: var(--rule); margin-bottom: 45px; }
</style>
</head>
<body>

<section class="card card--front" aria-label="Card front">
  <div class="holder">
    <p class="holder__name">Daniel Rourke</p>
    <p class="holder__role">Director of operations</p>
  </div>

  <div class="brand">
    <span class="brand__dot"></span>
    <p class="brand__name">BAYLINE PEST CARE</p>
  </div>

  <ul class="contacts">
    <li><svg viewBox="0 0 14 14"><rect x="3.5" y="0.5" width="7" height="13" rx="1.2"/><rect x="5" y="2.5" width="4" height="6" fill="#fff"/></svg>+ 000 000 0000</li>
    <li><svg viewBox="0 0 14 14"><path d="M1 5c0-2 2.5-3 6-3s6 1 6 3v1.2h-3V4.8H4v1.4H1z"/><path d="M3 7h8l1.5 6h-11z"/></svg>+ 000 000 0000</li>
    <li><svg viewBox="0 0 14 14"><rect x="0.5" y="2.5" width="13" height="9" rx="1"/><path d="M1 3.5l6 4.5 6-4.5" stroke="#fff" stroke-width="1.2" fill="none"/></svg>info@baylinepestcare.com</li>
    <li><svg viewBox="0 0 14 14"><circle cx="7" cy="7" r="6.3"/><path d="M0.7 7h12.6M7 0.7c-3 3.5-3 9 0 12.6M7 0.7c3 3.5 3 9 0 12.6" stroke="#fff" stroke-width="1" fill="none"/></svg>www.baylinepestcare.com</li>
  </ul>

  <address class="address">
    Level 4, 18 Harbour Lane<br>
    Suite 12 C<br>
    Brisbane, 40, Queensland
  </address>
</section>

<section class="card card--back" aria-label="Card back">
  <div class="brand">
    <span class="brand__dot"></span>
    <p class="brand__name">BAYLINE PEST CARE</p>
  </div>

  <div class="write-lines" aria-label="Lines for handwritten notes">
    <span></span><span></span><span></span><span></span>
  </div>
</section>

</body>
</html>
```